Northway Value Bureau (Account) WP Design

We need an Account (Profile) Wordpress design to add to nvb.co.uk.

The design should be based on https://nvb.co.uk/about/. The look and feel of the menu on the left.

The logic, after login the header menu will add another page:

Before Login:
Home / About / Trading / Support /

After Login
Home / About / Trading / Support / Account (Demo) - Logout

When you click on the / Account /

"Account Profile" page is loaded where you can change the settings etc.

"Account Profile" menu on the left should look the same as in / About / (https://nvb.co.uk/about/)

We need the following sub-pages under "Account Profile"

- Profile
- Transfers
- Reports
- Security
- API Key
- Affiliates

Now looking into each page:
-
- Profile (Should be split into individual or business) a user can choose whether how he want to run his account:

[Individual]

Personal Details
First Name:
Middle Name:
Family Name:
Citizenship:
Gender:
DOB:

[Attach File] (Government Issues ID, Passport, Driving License) - Verify

Contact Information
Phone: +44 207 555 0143 - Verify
E-Mail: sample@mailbox.example - Verify

Residential Address
Address line 1:
Address line 2:
Address line 3:
City:
Postcode:
Country:

[Attach File] (Utility Bill or Bank Statement) - Verify

[Business]

Company Name:
Registration Number:

Registered Address
Address line 1:
Address line 2:
Address line 3:
City:
Postcode:
Country:

[Attach File] (Certificate of Incorporation) - Verify
[Attach File] (Memorandum & Articles of Association)
[Attach File] (Shareholder Register)

Company Contact Information
Website:

-

- Transfers (Where a user can link a bank account to deposit or withdraw funds from the account)

Transfers

Add a bank account:

Please select the country where beneficiary’s bank is domicile: [Please select]
Please select the currency you wish to make transfers in: [Please select]

Full beneficiary name:
Full beneficiary address:
Beneficiary bank name:
Beneficiary bank address:
Beneficiary Bank Identification Code (BIC)/Routing Code:
Beneficiary IBAN number/account number:

[SAVE]

Deposti funds to NVB Bank Account
Amount of currency to be received e.g. 2345.67 [Please select: USD, EUR, GBP] :
Full beneficiary name: Northway Value Bureau Limited
Full beneficiary address: Kestrel Court
7-9 Fenwick Row
London, United Kingdom
Beneficiary bank name:
Beneficiary bank address:
Beneficiary Bank Identification Code (BIC)/Routing Code: XXXXXXXXXX
Beneficiary IBAN number/account number: XXXXXXXXXXXXXXXXXXXXXXXXXX

Deposit coins to NVB Coin Account
Amount of coins to be received e.g. 2345.67 [Please select: BTC, LTC]:
NVB Coin Account: XXXXXXXXXXXXXXXXXXXXXXXXXXXXX

Applicable charges (?):
[Clear] [Continue]

Withdraw funds from NVB Bank Account
Amount of currency to be sent e.g. 2345.67 [Please select: USD, EUR, GBP] :

Withdraw coins from NVB Coin Account:
Amount of coins to be sent e.g. 2345.67 [Please select: BTC, LTC]:
Please specify you coin account: XXXXXXXXXXXXXXXXXXXXXXXXXXXXX

Applicable charges (?):
[Clear] [Continue]

-

- Reports

TBC
-

- Security

Change Password
Current Password:
New Password:
Confirm New Password:

Enable / Disable : Two-factor Authentication (SMS)

-

- API Key
TBC

-
- Affiliates

Unlimited earning potential!
You'll receive up to 10% commission on all trades made through your affiliate link.

Referral Circle Scheme
Simply apply to our program from your publisher account or click the "Join Now" button below.

Corvalent.com - Join Now

```html
<!DOCTYPE html>
<html lang="en">
<head>
<meta charset="utf-8">
<title>Northway Value Bureau – Account Profile · Transfers</title>
<link href="https://fonts.googleapis.com/css2?family=Arimo:wght@400;700&display=swap" rel="stylesheet">
<style>
:root{
  --page-bg:#333333;
  --panel:#ffffff;
  --brand:#0a96d1;
  --brand-dark:#0679ab;
  --ink:#222222;
  --ink-soft:#444444;
  --muted:#7a7a7a;
  --field-border:#c9c9c9;
  --btn-dark:#444444;
}
*{box-sizing:border-box;margin:0;padding:0}
html,body{width:812px;height:1200px;overflow:hidden;background:var(--page-bg)}
body{font-family:"Arimo",Arial,sans-serif;color:var(--ink)}
.stage{position:relative;width:947px;height:1400px;transform:scale(0.85744);transform-origin:0 0}
.abs{position:absolute}
.panel{left:52px;top:0;width:843px;height:1372px;background:var(--panel)}

/* header */
.brand-name{left:130px;top:20px;font-size:14px;font-weight:700;color:var(--ink-soft);white-space:nowrap;display:flex;align-items:center;gap:7px}
.brand-name .dot{width:10px;height:10px;border-radius:50%;background:var(--brand);flex:none}
.main-nav{left:253px;top:46px;font-size:9px;color:#555}
.login-field{height:20px;border:1px solid var(--field-border);border-radius:2px;font-size:8.5px;color:#999;padding:4px 5px}
.help-dot{position:absolute;right:8px;top:3px;width:12px;height:12px;border:1px solid #aaa;border-radius:50%;font-size:8px;text-align:center;line-height:10px;color:#999}
.header-btn{top:29px;width:38px;height:16px;border-radius:2px;color:#fff;font-size:7.5px;font-weight:700;text-align:center;line-height:16px}

/* ticker */
.ticker{left:52px;top:71px;width:843px;height:34px;background:var(--brand)}
.coin-dot{left:219px;top:77px;width:23px;height:23px;border-radius:50%;border:2px solid #fff}
.stat{top:77px;color:#fff;white-space:nowrap}
.stat-label{font-size:7px;display:block}
.stat-value{font-size:10px;display:block;margin-top:2px}
.stat-value small{font-size:7px}
.stat-sep{top:74px;width:1px;height:28px;background:rgba(255,255,255,.45)}

/* side menu */
.page-title{left:203px;top:149px;font-size:14px;font-weight:700}
.side-menu{right:682px;top:183px;text-align:right;list-style:none}
.side-menu li{font-size:12px;font-weight:700;color:var(--muted);height:22.6px}
.side-menu li.is-active{color:var(--ink)}
.active-bar{left:284px;top:203px;width:2px;height:19px;background:var(--ink)}

/* form */
.section-title{left:359px;font-size:10.5px;font-weight:700;white-space:nowrap}
.label{right:509px;font-size:10px;color:var(--ink-soft);text-align:center;line-height:14px;white-space:nowrap}
.label-right{right:251px;font-size:10px;color:var(--ink-soft);white-space:nowrap}
.field{height:20px;border:1px solid var(--field-border);border-radius:2px;font-size:9px;padding:4px 8px;color:var(--ink);white-space:nowrap;overflow:hidden}
.field.filled{font-size:9.5px}
.select::after{content:"";position:absolute;right:8px;top:5px;width:5px;height:5px;border-right:1px solid #555;border-bottom:1px solid #555;transform:rotate(45deg)}
.select-currency{padding-left:14px;font-size:9.5px}
.hint{font-size:8.5px;color:#888;white-space:nowrap}
.q-dot{display:inline-block;width:11px;height:11px;border:1px solid #999;border-radius:50%;font-size:7px;text-align:center;line-height:9px;color:#999;vertical-align:middle;margin-left:2px}
.action-btn{height:20px;width:64px;background:var(--brand);color:#fff;font-size:8.5px;font-weight:700;border-radius:1px;overflow:hidden}
.action-btn .ico{position:absolute;left:0;top:0;width:20px;height:20px;background:var(--brand-dark)}
.action-btn .txt{position:absolute;left:20px;right:0;top:0;line-height:20px;text-align:center}

/* footer */
.footer{left:52px;top:1140px;width:843px;height:232px;background:var(--brand)}
.footer-brand{left:130px;top:1180px;font-size:14px;font-weight:700;color:#fff;white-space:nowrap;display:flex;align-items:center;gap:7px}
.footer-brand .dot{width:10px;height:10px;border-radius:50%;background:#fff;flex:none}
.footer-col-title{top:1168px;font-size:16px;font-weight:700;color:#fff;white-space:nowrap}
.footer-links{top:1196px;list-style:none;font-size:8px;color:#fff;line-height:10.5px}
.social-dot{top:1197px;width:19px;height:19px;border-radius:50%;background:#fff}
.copyright{left:130px;top:1227px;font-size:7px;color:#fff;line-height:10px}
.tagline-art{left:405px;top:1285px;width:405px;height:50px;background:linear-gradient(90deg,rgba(255,255,255,.08),rgba(255,255,255,.35),rgba(255,255,255,.15))}
</style>
</head>
<body>
<div class="stage">
  <div class="abs panel"></div>

  <!-- header -->
  <div class="abs brand-name">Northway Value Bureau<span class="dot"></span></div>
  <div class="abs main-nav">Home · About · Trading · Support · Account (Demo) - Logout</div>
  <div class="abs login-field" style="left:539px;top:27px;width:94px">Email<span class="help-dot">?</span></div>
  <div class="abs login-field" style="left:637px;top:27px;width:94px">Password<span class="help-dot">?</span></div>
  <div class="abs header-btn" style="left:736px;background:var(--btn-dark)">Log In</div>
  <div class="abs header-btn" style="left:779px;background:var(--brand)">Sign Up</div>

  <!-- ticker -->
  <div class="abs ticker"></div>
  <div class="abs coin-dot"></div>
  <div class="abs stat" style="left:250px"><span class="stat-label">Current Price</span><span class="stat-value">$444.13</span></div>
  <div class="abs stat-sep" style="left:320px"></div>
  <div class="abs stat" style="left:330px"><span class="stat-label">Daily Change</span><span class="stat-value">-9.54 <small>▾2.10%</small></span></div>
  <div class="abs stat-sep" style="left:409px"></div>
  <div class="abs stat" style="left:418px"><span class="stat-label">Day's Range</span><span class="stat-value">$440.00 - $457.30</span></div>
  <div class="abs stat-sep" style="left:525px"></div>
  <div class="abs stat" style="left:536px"><span class="stat-label">Today's Open</span><span class="stat-value">$453.57</span></div>
  <div class="abs stat-sep" style="left:600px"></div>
  <div class="abs stat" style="left:619px"><span class="stat-label">24h Volume</span><span class="stat-value">7194 BTC</span></div>

  <!-- side menu -->
  <h1 class="abs page-title">Account Profile</h1>
  <ul class="abs side-menu">
    <li>Profile</li>
    <li class="is-active">Transfers</li>
    <li>Reports</li>
    <li>Security</li>
    <li>API Key</li>
    <li>Affiliates</li>
  </ul>
  <div class="abs active-bar"></div>

  <!-- add a bank account -->
  <h2 class="abs section-title" style="top:189px">Add a bank account</h2>
  <div class="abs label" style="top:219px">Beneficiary's bank country:</div>
  <div class="abs field select" style="left:451px;top:216px;width:150px"></div>
  <div class="abs hint" style="left:606px;top:221px">Please select the country where beneficiary's bank is domicile.</div>
  <div class="abs label" style="top:247px">Currency transfers:</div>
  <div class="abs field select" style="left:451px;top:244px;width:150px"></div>
  <div class="abs hint" style="left:606px;top:249px">Please select the currency you wish to make transfers in.</div>
  <div class="abs label" style="top:275px">Full beneficiary name:</div>
  <div class="abs field" style="left:451px;top:272px;width:150px"></div>
  <div class="abs label" style="top:303px">Full beneficiary address:</div>
  <div class="abs field" style="left:451px;top:300px;width:150px"></div>
  <div class="abs label" style="top:331px">Beneficiary bank name:</div>
  <div class="abs field" style="left:451px;top:328px;width:150px"></div>
  <div class="abs label" style="top:359px">Beneficiary Bank<br>Identification Code (BIC):</div>
  <div class="abs field" style="left:451px;top:363px;width:158px"></div>
  <div class="abs label-right" style="top:367px">Routing Code:</div>
  <div class="abs field" style="left:705px;top:363px;width:49px"></div>
  <div class="abs label" style="top:401px">Beneficiary IBAN number:</div>
  <div class="abs field" style="left:451px;top:398px;width:158px"></div>
  <div class="abs label-right" style="top:402px">Account number:</div>
  <div class="abs field" style="left:705px;top:398px;width:157px"></div>
  <div class="abs action-btn" style="left:627px;top:444px;width:63px"><span class="ico"><svg width="20" height="20" viewBox="0 0 20 20"><rect x="5" y="5" width="10" height="10" fill="none" stroke="#fff" stroke-width="1.2"/><rect x="7.5" y="5" width="5" height="3.5" fill="#fff"/></svg></span><span class="txt">Save</span></div>

  <!-- deposit funds -->
  <h2 class="abs section-title" style="top:484px">Deposit funds to NVB Bank Account</h2>
  <div class="abs label" style="top:514px">Amount of currency to be received:</div>
  <div class="abs field" style="left:451px;top:510px;width:109px"></div>
  <div class="abs field select select-currency" style="left:568px;top:510px;width:54px">USD</div>
  <div class="abs hint" style="left:628px;top:515px">e.g. 2345.67</div>
  <div class="abs label" style="top:542px">Full beneficiary name:</div>
  <div class="abs field" style="left:451px;top:539px;width:150px;font-size:8.5px">Northway Value Bureau Limited</div>
  <div class="abs label" style="top:570px">Full beneficiary address:</div>
  <div class="abs field" style="left:451px;top:567px;width:150px">Kestrel Court</div>
  <div class="abs field" style="left:451px;top:595px;width:150px">7-9 Fenwick Row</div>
  <div class="abs field" style="left:451px;top:623px;width:150px">London, United Kingdom</div>
  <div class="abs label" style="top:655px">Beneficiary bank name:</div>
  <div class="abs field" style="left:451px;top:651px;width:150px"></div>
  <div class="abs label" style="top:683px">Beneficiary bank address:</div>
  <div class="abs field" style="left:451px;top:679px;width:150px"></div>
  <div class="abs label" style="top:710px">Beneficiary Bank<br>Identification Code (BIC):</div>
  <div class="abs field filled" style="left:451px;top:714px;width:158px">XXXX - XXXX - XXXX - XXXX</div>
  <div class="abs label-right" style="top:718px">Routing Code:</div>
  <div class="abs field filled" style="left:705px;top:714px;width:49px">123</div>
  <div class="abs label" style="top:753px">Beneficiary IBAN number:</div>
  <div class="abs field filled" style="left:451px;top:749px;width:158px">XXXX - XXXX - XXXX - XXXX</div>
  <div class="abs label-right" style="top:753px">Account number:</div>
  <div class="abs field filled" style="left:705px;top:749px;width:157px">XXXX - XXXX - XXXX - XXXX</div>
  <div class="abs label" style="top:788px;right:507px">Applicable charges <span class="q-dot">?</span> :</div>
  <div class="abs field" style="left:451px;top:784px;width:156px"></div>
  <div class="abs action-btn" style="left:556px;top:831px"><span class="ico"><svg width="20" height="20" viewBox="0 0 20 20"><path d="M5 10l3-3h7v6H8z" fill="#fff"/></svg></span><span class="txt">Clear</span></div>
  <div class="abs action-btn" style="left:627px;top:831px"><span class="ico"><svg width="20" height="20" viewBox="0 0 20 20"><path d="M6 5l9 5-9 5 2-5z" fill="#fff"/></svg></span><span class="txt">Continue</span></div>

  <!-- withdraw funds -->
  <h2 class="abs section-title" style="top:878px">Withdraw funds from NVB Bank Account</h2>
  <div class="abs label" style="top:908px">Amount of currency to be sent:</div>
  <div class="abs field" style="left:451px;top:904px;width:109px"></div>
  <div class="abs field select select-currency" style="left:568px;top:904px;width:54px">USD</div>
  <div class="abs hint" style="left:628px;top:909px">e.g. 2345.67</div>

  <!-- withdraw coins -->
  <h2 class="abs section-title" style="top:948px">Withdraw coins from NVB Coin Account</h2>
  <div class="abs label" style="top:978px">Amount of currency to be sent:</div>
  <div class="abs field" style="left:451px;top:974px;width:109px"></div>
  <div class="abs field select select-currency" style="left:568px;top:974px;width:54px">USD</div>
  <div class="abs hint" style="left:628px;top:979px">e.g. 2345.67</div>
  <div class="abs label" style="top:1013px">Beneficiary IBAN number:</div>
  <div class="abs field filled" style="left:451px;top:1009px;width:158px">XXXXXXXXXXXXXXXXXXXX</div>
  <div class="abs label" style="top:1048px;right:507px">Applicable charges <span class="q-dot">?</span> :</div>
  <div class="abs field" style="left:451px;top:1044px;width:156px"></div>
  <div class="abs action-btn" style="left:556px;top:1090px"><span class="ico"><svg width="20" height="20" viewBox="0 0 20 20"><path d="M5 10l3-3h7v6H8z" fill="#fff"/></svg></span><span class="txt">Clear</span></div>
  <div class="abs action-btn" style="left:627px;top:1090px"><span class="ico"><svg width="20" height="20" viewBox="0 0 20 20"><path d="M6 5l9 5-9 5 2-5z" fill="#fff"/></svg></span><span class="txt">Continue</span></div>

  <!-- footer -->
  <div class="abs footer"></div>
  <div class="abs footer-brand">Northway Value Bureau<span class="dot"></span></div>
  <div class="abs copyright">© 2014 Northway Value Bureau.<br>All rights reserved</div>

  <div class="abs footer-col-title" style="left:368px">ABOUT US</div>
  <ul class="abs footer-links" style="left:368px">
    <li>Rulebook</li><li>Trading Fees</li><li>Partners</li><li>Security</li><li>Terms of Service</li><li>Privacy Policy</li><li>Latest News</li>
  </ul>
  <div class="abs footer-col-title" style="left:548px">SUPPORT</div>
  <ul class="abs footer-links" style="left:548px">
    <li>What is Bitcoin?</li><li>How to buy a bitcoin?</li><li>How to sell a bitcoin?</li>
  </ul>
  <div class="abs footer-col-title" style="left:710px">FOLLOW NVB</div>
  <div class="abs social-dot" style="left:710px"></div>
  <div class="abs social-dot" style="left:738px"></div>
  <div class="abs social-dot" style="left:766px"></div>
  <div class="abs social-dot" style="left:794px"></div>

  <div class="abs tagline-art" role="img" aria-label="Hand-lettered tagline: Change the world one bitcoin at a time"></div>
</div>
</body>
</html>
```